Real Estate Brokerage Stationery Designs

I am looking to have presentation folders with business card slots on both sides along with pockets on both sides. I've attached logos, website colors along with current business card designs.

I am looking for envelope designs both big and small. Possibly new business card designs, notepad templates for big and small notepads. Letterhead designs. Pop socket designs. Realtors name badge designs.

www.brightholdrealty.example

```html
<!DOCTYPE html>
<html lang="en">
<head>
<meta charset="utf-8">
<title>Brighthold Realty Stationery</title>
<link href="https://fonts.googleapis.com/css2?family=Roboto:wght@400;500&display=swap" rel="stylesheet">
<style>
  :root {
    --backdrop: #a9a8a9;
    --paper: #f5f4f2;
    --brand-blue: #0a56a8;
    --ink: #2b2b2b;
    --muted: #5a5a5a;
    --rule: #9c9c9c;
    --ghost-a: #e3e7ee;
    --ghost-b: #eceef1;
    --coil: #2a2a2a;
  }
  html, body { margin: 0; padding: 0; overflow: hidden; }
  body {
    width: 1074px; height: 1200px; position: relative;
    background: var(--backdrop);
    font-family: "Roboto", Arial, sans-serif; color: var(--ink);
  }
  .sheet {
    position: absolute; background: var(--paper);
    box-shadow: 0 2px 6px rgba(0,0,0,.25); overflow: hidden;
  }
  .brand { display: flex; align-items: center; gap: 5px; position: absolute; white-space: nowrap; }
  .brand-mark { background: var(--brand-blue); flex: none; }
  .brand-name { color: var(--brand-blue); font-weight: 500; }
  .ghost-art {
    position: absolute;
    background: linear-gradient(180deg, var(--ghost-b) 0%, var(--ghost-a) 100%);
    border-radius: 4px 4px 0 0;
  }
  .return-address { position: absolute; font-size: 7px; line-height: 9.5px; color: var(--muted); }

  /* Letterhead */
  .letterhead { left: 54px; top: 32px; width: 438px; height: 617px; }
  .letterhead .brand { left: 44px; top: 66px; }
  .letterhead .brand-mark { width: 12px; height: 12px; }
  .letterhead .brand-name { font-size: 13px; }
  .letterhead .address { position: absolute; right: 145px; top: 54px; text-align: right; font-size: 7.5px; line-height: 10px; color: var(--muted); }
  .letterhead .divider { position: absolute; left: 299px; top: 54px; width: 1px; height: 42px; background: #cfcfcf; }
  .letterhead .contacts { position: absolute; left: 307px; top: 54px; font-size: 7.5px; line-height: 10px; color: var(--muted); }
  .contacts .row { display: flex; align-items: center; gap: 4px; }
  .contacts svg { width: 7px; height: 7px; fill: var(--brand-blue); }
  .letterhead .ghost-art { left: 0; right: 0; bottom: 0; height: 362px; }

  /* Envelope back with flap */
  .envelope-back { left: 526px; top: 169px; width: 492px; height: 224px; }
  .envelope-back .flap {
    position: absolute; left: 0; right: 0; top: 0; height: 82px;
    background: var(--brand-blue); border-radius: 0 0 26px 26px;
    display: flex; align-items: center; justify-content: center;
  }
  .flap-mark { width: 12px; height: 12px; background: var(--paper); }

  /* Envelope front */
  .envelope-front { left: 527px; top: 425px; width: 493px; height: 224px; }
  .envelope-front .brand { left: 19px; top: 66px; }
  .envelope-front .brand-mark { width: 11px; height: 11px; }
  .envelope-front .brand-name { font-size: 12px; }
  .envelope-front .return-address { left: 19px; top: 103px; }
  .envelope-front .ghost-art { left: 230px; width: 250px; bottom: 0; height: 190px; }

  /* A4 envelope */
  .envelope-a4 { left: 38px; top: 726px; width: 282px; height: 435px; overflow: visible; box-shadow: none; background: none; }
  .envelope-a4 .flap {
    position: absolute; left: 2px; right: 2px; top: 0; height: 36px;
    background: var(--brand-blue); border-radius: 14px 14px 0 0;
    display: flex; align-items: center; justify-content: center;
  }
  .envelope-a4 .flap-mark { width: 9px; height: 9px; }
  .envelope-a4 .body { position: absolute; left: 0; right: 0; top: 36px; bottom: 0; background: var(--paper); box-shadow: 0 2px 6px rgba(0,0,0,.25); overflow: hidden; }
  .envelope-a4 .brand { left: 12px; top: 40px; }
  .envelope-a4 .brand-mark { width: 8px; height: 8px; }
  .envelope-a4 .brand-name { font-size: 9px; }
  .envelope-a4 .return-address { left: 12px; top: 67px; font-size: 5.5px; line-height: 7.5px; }
  .envelope-a4 .ghost-art { left: 16px; width: 190px; bottom: 0; height: 220px; }
  .caption { position: absolute; left: 38px; width: 282px; top: 1168px; text-align: center; font-size: 11px; font-weight: 500; color: #111; }

  /* Notepads */
  .coil {
    position: absolute; left: 6px; right: 6px; top: -6px; height: 14px;
    background: repeating-linear-gradient(90deg, var(--coil) 0 2px, transparent 2px 7px);
  }
  .notepad-large { left: 357px; top: 718px; width: 346px; height: 449px; overflow: visible; }
  .notepad-large .brand { left: 50%; transform: translateX(-50%); top: 48px; }
  .notepad-large .brand-mark { width: 10px; height: 10px; }
  .notepad-large .brand-name { font-size: 11px; }
  .notepad-large .ghost-art { left: 22px; width: 240px; bottom: 0; height: 250px; }
  .lines { position: absolute; left: 27px; right: 31px; top: 96px; }
  .lines span { display: block; height: 19.6px; border-top: 1px solid var(--rule); box-sizing: border-box; position: relative; }
  .pad-url { position: absolute; left: 0; right: 0; text-align: center; font-size: 8px; letter-spacing: 2.4px; color: var(--muted); }
  .notepad-large .pad-url { top: 424px; }

  .tent-card { left: 745px; top: 720px; width: 268px; height: 192px; overflow: visible;
    background: linear-gradient(90deg, #e6e4e1 0%, #f4f3f1 40%, #e4e2df 100%); }
  .tent-card .fold { position: absolute; right: -26px; top: 6px; width: 26px; height: 180px; background: #fbfbfb; clip-path: polygon(0 0, 40% 0, 100% 100%, 0 100%); }
  .tent-card .brand { left: 50%; transform: translateX(-50%); top: 110px; }
  .tent-card .brand-mark { width: 14px; height: 14px; }
  .tent-card .brand-name { font-size: 15px; }

  .notepad-small { left: 746px; top: 974px; width: 269px; height: 192px; overflow: visible; }
  .notepad-small .brand { left: 50%; transform: translateX(-50%); top: 44px; }
  .notepad-small .brand-mark { width: 8px; height: 8px; }
  .notepad-small .brand-name { font-size: 9px; }
  .notepad-small .lines { left: 27px; right: 23px; top: 70px; }
  .notepad-small .lines span { height: 18.6px; }
  .notepad-small .pad-url { top: 169px; font-size: 7.5px; }
</style>
</head>
<body>

<section class="sheet letterhead">
  <div class="brand"><span class="brand-mark"></span><span class="brand-name">Brighthold Realty</span></div>
  <div class="address">742 Harbor View Rd<br>Suite 310<br>Lakeside, FL 33990<br>www.brightholdrealty.example</div>
  <div class="divider"></div>
  <div class="contacts">
    <div class="row"><svg viewBox="0 0 10 10"><path d="M2 0h2l1 3-1.5 1a6 6 0 0 0 2.5 2.5L7 5l3 1v2c0 1-1 2-2 2A8 8 0 0 1 0 2c0-1 1-2 2-2z"/></svg>555-014-2201</div>
    <div class="row"><svg viewBox="0 0 10 10"><path d="M2.5 0h5v10h-5zM3.5 1v7h3V1z"/></svg>555-014-2202</div>
    <div class="row"><svg viewBox="0 0 10 10"><path d="M2 0h6v3H2zM0 4h10v4H8v2H2V8H0z"/></svg>555-014-2203</div>
    <div class="row"><svg viewBox="0 0 10 10"><path d="M0 2h10v1L5 6 0 3zM0 4l5 3 5-3v4H0z"/></svg>hello@brightholdrealty.example</div>
  </div>
  <div class="ghost-art" role="img" aria-label="Faint illustration of city towers and house rooftops"></div>
</section>

<section class="sheet envelope-back">
  <div class="flap"><span class="flap-mark"></span></div>
</section>

<section class="sheet envelope-front">
  <div class="brand"><span class="brand-mark"></span><span class="brand-name">Brighthold Realty</span></div>
  <div class="return-address">742 Harbor View Rd, Suite 310,<br>Lakeside, FL 33990</div>
  <div class="ghost-art" role="img" aria-label="Faint illustration of city towers and house rooftops"></div>
</section>

<section class="sheet envelope-a4">
  <div class="flap"><span class="flap-mark"></span></div>
  <div class="body">
    <div class="brand"><span class="brand-mark"></span><span class="brand-name">Brighthold Realty</span></div>
    <div class="return-address">742 Harbor View Rd, Suite 310,<br>Lakeside, FL 33990</div>
    <div class="ghost-art" role="img" aria-label="Faint illustration of city towers and house rooftops"></div>
  </div>
</section>
<div class="caption">Envelope A4</div>

<section class="sheet notepad-large">
  <div class="coil"></div>
  <div class="ghost-art" role="img" aria-label="Faint illustration of city towers and house rooftops"></div>
  <div class="brand"><span class="brand-mark"></span><span class="brand-name">Brighthold Realty</span></div>
  <div class="lines">
    <span></span><span></span><span></span><span></span><span></span><span></span><span></span><span></span><span></span><span></span><span></span><span></span><span></span><span></span><span></span><span></span><span></span>
  </div>
  <div class="pad-url">www.brightholdrealty.example</div>
</section>

<section class="sheet tent-card">
  <div class="coil"></div>
  <div class="fold"></div>
  <div class="brand"><span class="brand-mark"></span><span class="brand-name">Brighthold Realty</span></div>
</section>

<section class="sheet notepad-small">
  <div class="coil"></div>
  <div class="brand"><span class="brand-mark"></span><span class="brand-name">Brighthold Realty</span></div>
  <div class="lines"><span></span><span></span><span></span><span></span><span></span><span></span></div>
  <div class="pad-url">www.brightholdrealty.example</div>
</section>

</body>
</html>
```